International business needs business cards

Our company, DRV Ventures Inc. is in the business of supplying a range construction products with particular emphasis on CEMENT. We have developed our own brand - TORVAN SUPPLIES - with which to infiltrate the market. We are launching our brand of cement (TORVAN Type IS Cement) into the Caribbean which is unlike anything this market has ever seen. A monopoly has existed here for the past 60-odd years and the market has now opened to allow the importation of other brands and consumers are anxious and ready for change/improvement. We are very excited to be launching and want to make a great first impression. We will be conducting workshops and seminars (from government level to the hardware store owners) and we want our business card to give us the strong, confident introduction that we need.

Target Market(s)

construction; builders; engineers; home owners

Industry/Entity Type

Construction

Contact Information for Business Card

Marisol Depree
CEO
cell # 1 555 4180736
Ground floor,Lindell Plaza Suite 2734
George Town,Grand Cayman
Cayman Islands,KY1-4823
EMAIL: m.depree@drvventuresinc.example
web site drvventuresinc.example

COMPANY: skype info drv.ventures.example

second card
Yvette Brannock-Depree
CFO
CELL# 1 555 607 3941
George Town,Grand Cayman
Cayman Islands,KY1-4823
EMAIL: y.brannockdepree@drvventuresinc.example
website drvventuresinc.example

Requirements
Must have
• Business cards must display BOTH logos - DRV is the company and TORVAN is the brand.

```html
<!DOCTYPE html>
<html lang="en">
<head>
<meta charset="utf-8">
<title>DRV Ventures Inc. — Business Cards</title>
<link href="https://fonts.googleapis.com/css2?family=Open+Sans:wght@400;600;700;800&display=swap" rel="stylesheet">
<style>
  :root {
    --backdrop: #e9e6e1;
    --card-white: #ffffff;
    --card-shade: #f1f1f1;
    --wine: #8c1d24;
    --wine-deep: #6a1217;
    --ink: #141414;
    --ink-soft: #555555;
    --brand-grey: #5a5a5a;
    --on-wine: #ffffff;
    --on-wine-soft: #f1d9da;
    --mark-faint: #ece8e8;
    --divider: #1a1a1a;
  }
  * { box-sizing: border-box; margin: 0; padding: 0; }
  html, body {
    width: 1200px; height: 843px; overflow: hidden;
    background: var(--backdrop);
    font-family: "Open Sans", Arial, sans-serif;
  }
  .stage { position: relative; width: 1200px; height: 843px; }
  .card {
    position: absolute; left: 290px;
    width: 620px; height: 354px;
    background: linear-gradient(135deg, var(--card-white) 55%, var(--card-shade));
    box-shadow: 0 6px 18px rgba(0,0,0,.18);
    overflow: hidden;
  }
  .card--back { top: 50px; }
  .card--front { top: 439px; display: flex; }

  /* shared company name block */
  .wordmark {
    display: flex; align-items: center; gap: 12px;
    color: var(--ink); font-weight: 800; white-space: nowrap;
  }
  .wordmark__square { background: var(--wine); flex: none; }
  .wordmark__text { display: flex; flex-direction: column; line-height: 1; }
  .wordmark__main { letter-spacing: 1px; }
  .wordmark__sub { letter-spacing: .5px; margin-top: 4px; }

  /* back card */
  .back-panel {
    position: absolute; right: 0; top: 0;
    width: 300px; height: 200px;
    background: var(--mark-faint);
  }
  .back-identity { position: absolute; left: 44px; bottom: 50px; }
  .back-identity .wordmark__square { width: 56px; height: 56px; }
  .back-identity .wordmark__main { font-size: 64px; }
  .back-identity .wordmark__sub { font-size: 17px; }
  .back-web {
    margin-top: 8px; font-size: 15px; font-weight: 600; color: var(--ink-soft);
  }

  /* front card */
  .contact-side {
    width: 312px; height: 100%;
    background: linear-gradient(160deg, var(--wine) 0%, var(--wine-deep) 100%);
    color: var(--on-wine);
    padding: 30px 24px 0 30px;
  }
  .contact-side__rule { width: 9px; height: 100%; background: var(--divider); flex: none; }
  .person__name { font-size: 21px; font-weight: 700; line-height: 1.2; }
  .person__title { font-size: 13px; color: var(--on-wine-soft); }
  .dots { border-top: 2px dotted rgba(255,255,255,.75); margin: 16px 0 14px; }
  .address { font-size: 14px; line-height: 1.35; }
  .channels { list-style: none; font-size: 14px; line-height: 1.65; }
  .channels li { display: flex; align-items: center; gap: 10px; white-space: nowrap; }
  .channels svg { width: 14px; height: 14px; flex: none; }

  .brand-side {
    flex: 1; display: flex; flex-direction: column;
    align-items: center; justify-content: center; gap: 34px;
    padding: 0 20px;
  }
  .brand-side .wordmark__square { width: 40px; height: 40px; }
  .brand-side .wordmark__main { font-size: 44px; }
  .brand-side .wordmark__sub { font-size: 12px; }
  .product-brand {
    display: flex; align-items: center; gap: 10px;
    color: var(--brand-grey); font-weight: 700; font-size: 16px;
    letter-spacing: 2px; white-space: nowrap;
  }
  .product-brand__dot {
    width: 26px; height: 26px; border-radius: 50%;
    background: var(--brand-grey); flex: none;
  }
</style>
</head>
<body>
<main class="stage">

  <section class="card card--back" aria-label="Business card, company side">
    <div class="back-panel"></div>
    <div class="back-identity">
      <div class="wordmark">
        <span class="wordmark__square"></span>
        <span class="wordmark__text">
          <span class="wordmark__main">DRV</span>
          <span class="wordmark__sub">VENTURES INC.</span>
        </span>
      </div>
      <p class="back-web">www.drvventuresinc.example</p>
    </div>
  </section>

  <section class="card card--front" aria-label="Business card, contact side">
    <div class="contact-side">
      <h1 class="person__name">Marisol Depree</h1>
      <p class="person__title">CEO</p>
      <div class="dots"></div>
      <p class="address">Ground floor<br>Lindell Plaza Suite 2734<br>George Town,Grand Cayman<br>Cayman Islands,KY1-4823</p>
      <div class="dots"></div>
      <ul class="channels">
        <li>
          <svg viewBox="0 0 14 14" aria-hidden="true"><rect x="3.5" y="0.5" width="7" height="13" rx="1.5" fill="none" stroke="currentColor" stroke-width="1.3"/><circle cx="7" cy="11.2" r="0.9" fill="currentColor"/></svg>
          1 555 4180736
        </li>
        <li>
          <svg viewBox="0 0 14 14" aria-hidden="true"><rect x="0.5" y="2.5" width="13" height="9" fill="currentColor"/><path d="M0.8 3 L7 8 L13.2 3" fill="none" stroke="#7a161c" stroke-width="1.2"/></svg>
          m.depree@drvventuresinc.example
        </li>
        <li>
          <svg viewBox="0 0 14 14" aria-hidden="true"><circle cx="7" cy="7" r="6.2" fill="none" stroke="currentColor" stroke-width="1.2"/><ellipse cx="7" cy="7" rx="2.6" ry="6.2" fill="none" stroke="currentColor" stroke-width="1"/><line x1="0.8" y1="7" x2="13.2" y2="7" stroke="currentColor" stroke-width="1"/></svg>
          www.drvventuresinc.example
        </li>
      </ul>
    </div>
    <div class="contact-side__rule"></div>
    <div class="brand-side">
      <div class="wordmark">
        <span class="wordmark__square"></span>
        <span class="wordmark__text">
          <span class="wordmark__main">DRV</span>
          <span class="wordmark__sub">VENTURES INC.</span>
        </span>
      </div>
      <div class="product-brand">
        <span class="product-brand__dot"></span>TORVAN SUPPLIES
      </div>
    </div>
  </section>

</main>
</body>
</html>
```